Vale Crest - Business Cards

We are a consultancy to help builders to optimize their planning in order to save building costs. For that reason we need a clean and professional business card for our high-priced services. A QR code should lead to the contact information needed.

```html
<!DOCTYPE html>
<html lang="en">
<head>
<meta charset="utf-8">
<title>Vale Crest – Business Cards</title>
<link href="https://fonts.googleapis.com/css2?family=Roboto:wght@400;500;700&display=swap" rel="stylesheet">
<style>
  :root {
    --bg: #2b2b2c;
    --ink: #2e2d31;
    --ink-soft: #3a393d;
    --paper: #efefef;
    --gold-dark: #9c6a24;
    --gold-mid: #c99a42;
    --gold-light: #e6c266;
  }
  * { margin: 0; padding: 0; box-sizing: border-box; }
  html, body {
    width: 1200px; height: 1138px; overflow: hidden;
    background: var(--bg);
    font-family: "Roboto", Arial, sans-serif;
  }
  .card {
    position: absolute;
    border-radius: 16px;
    overflow: hidden;
    box-shadow: 0 6px 14px rgba(0,0,0,0.45);
  }
  .card-front {
    left: 274px; top: 186px; width: 623px; height: 376px;
    background: linear-gradient(35deg, var(--gold-dark) 0%, var(--gold-mid) 45%, var(--gold-light) 100%);
  }
  .front-lockup {
    position: absolute; left: 0; right: 0; top: 150px;
    text-align: center; color: var(--ink);
  }
  .brand-name {
    font-weight: 700; font-size: 42px; letter-spacing: 3px; text-transform: uppercase;
  }
  .brand-tagline {
    font-weight: 700; font-size: 16px; letter-spacing: 4px; text-transform: uppercase; margin-top: 2px;
  }
  .card-back {
    left: 276px; top: 608px; width: 618px; height: 374px;
    background: var(--paper);
  }
  .back-shape { position: absolute; inset: 0; }
  .back-lockup {
    position: absolute; left: 0; width: 290px; top: 165px;
    text-align: center; color: var(--ink);
  }
  .back-lockup .brand-name { font-size: 26px; letter-spacing: 2px; }
  .back-lockup .brand-tagline { font-size: 10.5px; letter-spacing: 3px; margin-top: 0; }
  .contact {
    position: absolute; right: 39px; top: 86px;
    text-align: right; color: var(--ink-soft);
  }
  .person-name { font-weight: 700; font-size: 24px; color: var(--ink); line-height: 28px; }
  .person-role { font-size: 16px; line-height: 20px; }
  .address { margin-top: 26px; font-size: 16px; line-height: 24px; }
  .contact-list { list-style: none; margin-top: 6px; margin-right: -31px; }
  .contact-list li {
    font-size: 16px; line-height: 23.5px;
    display: flex; justify-content: flex-end; align-items: center; gap: 14px;
  }
  .contact-list svg { width: 16px; height: 14px; fill: var(--gold-mid); }
</style>
</head>
<body>
  <section class="card card-front">
    <div class="front-lockup">
      <div class="brand-name">Vale Crest</div>
      <div class="brand-tagline">Plan smart, build lean</div>
    </div>
  </section>

  <section class="card card-back">
    <svg class="back-shape" viewBox="0 0 618 374" preserveAspectRatio="none">
      <defs>
        <linearGradient id="goldBand" x1="0" y1="0" x2="0" y2="1">
          <stop offset="0" stop-color="#ae7d2e"/>
          <stop offset="0.5" stop-color="#e4be60"/>
          <stop offset="1" stop-color="#a3722a"/>
        </linearGradient>
      </defs>
      <path d="M268 0 H294 Q404 187 268 374 Z" fill="#3a393e"/>
      <path d="M0 0 H268 Q398 187 268 374 H0 Z" fill="url(#goldBand)"/>
    </svg>
    <div class="back-lockup">
      <div class="brand-name">Vale Crest</div>
      <div class="brand-tagline">Plan smart, build lean</div>
    </div>
    <div class="contact">
      <div class="person-name">Vale Crest</div>
      <div class="person-role">Managing Director</div>
      <div class="address">18 Meadow Lane, Elmfield,<br>Northvale, 40231</div>
      <ul class="contact-list">
        <li>555-014-2290
          <svg viewBox="0 0 16 14" aria-hidden="true"><path d="M1 5 Q8 0 15 5 L13 7 L11 5 H5 L3 7 Z M4 8 H12 L14 13 H2 Z"/></svg>
        </li>
        <li>office@valecrest.com
          <svg viewBox="0 0 16 14" aria-hidden="true"><path d="M1 2 H15 V12 H1 Z M2 3 L8 8 L14 3 Z" fill-rule="evenodd"/></svg>
        </li>
        <li>www.valecrest.com
          <svg viewBox="0 0 16 14" aria-hidden="true"><circle cx="8" cy="7" r="6.5"/><path d="M8 0.5 V13.5 M1.5 7 H14.5" stroke="#efefef" stroke-width="1"/></svg>
        </li>
      </ul>
    </div>
  </section>
</body>
</html>
```